Birchline Septic Solutions

Would like to see some single sided ones but would also like to see some double sided with one sided only being the logo. Owners name is Colin Vandro. Phone number is 555-214-0387
Services are pumping, inspections, installs, and repairs

Contact Information for Business Card

555-241-0387 Colin Vandro Cedarvale, OH

```html
<!DOCTYPE html>
<html lang="en">
<head>
<meta charset="utf-8">
<title>Birchline Septic Solutions – Business Card</title>
<link rel="stylesheet" href="https://fonts.googleapis.com/css2?family=Open+Sans:wght@400;600;700&display=swap">
<style>
  :root {
    --stage: #232323;
    --card: #1e1e21;
    --teal: #27bfb8;
    --white: #ffffff;
    --rule: #8a8a8a;
  }
  * { box-sizing: border-box; margin: 0; padding: 0; }
  html, body {
    width: 1200px; height: 779px; overflow: hidden;
    background: var(--stage);
    font-family: "Open Sans", Arial, sans-serif;
  }
  .stage { position: relative; width: 1200px; height: 779px; }
  .card {
    position: absolute; width: 540px; height: 309px;
    background: var(--card);
    box-shadow: 0 18px 40px rgba(0,0,0,.55);
    overflow: hidden;
  }
  .card--back { left: 45px; top: 235px; }
  .card--front { left: 615px; top: 235px; }

  /* back */
  .back-pattern {
    position: absolute; inset: 0;
    background: linear-gradient(200deg, #6d6d6f 0%, #3a3a3c 28%, #1a1a1c 55%, #111113 100%);
  }
  .back-name {
    position: absolute; right: 58px; top: 160px;
    color: var(--white); font-weight: 700; font-size: 17px;
    text-align: center; line-height: 1.15; letter-spacing: .5px;
    text-transform: uppercase;
  }

  /* front */
  .brand-name {
    position: absolute; left: 40px; top: 118px; width: 210px;
    color: var(--white); font-weight: 700; font-size: 24px;
    text-align: center; line-height: 1.1; text-transform: uppercase;
    letter-spacing: .5px;
  }
  .divider {
    position: absolute; left: 278px; top: 70px; width: 1px; height: 120px;
    background: var(--rule);
  }
  .contact { position: absolute; left: 300px; top: 90px; color: var(--white); }
  .contact__name { font-size: 27px; font-weight: 700; line-height: 1.1; }
  .contact__first { color: var(--teal); }
  .contact__city { font-size: 15px; margin-top: 4px; }
  .contact__phone { font-size: 15px; margin-top: 4px; display: flex; align-items: center; gap: 7px; }
  .contact__phone svg { width: 14px; height: 14px; }

  .services-band {
    position: absolute; left: 0; right: 0; top: 240px; height: 32px;
    background: var(--teal);
    display: flex; align-items: center; padding-left: 110px; gap: 8px;
    color: var(--white); font-size: 15px; font-weight: 600;
  }
  .services-band .dot {
    width: 9px; height: 9px; border-radius: 50%; background: var(--white);
  }
  .services-badge {
    position: absolute; left: 255px; top: 220px; width: 100px; height: 26px;
    border-radius: 50%; background: var(--teal);
    border: 1.5px solid var(--white);
    color: var(--white); font-size: 13px; font-weight: 700;
    display: flex; align-items: center; justify-content: center;
  }
</style>
</head>
<body>
<main class="stage">
  <section class="card card--back" aria-label="Card back">
    <div class="back-pattern" role="img" aria-label="Repeating mountain and pine tree brand pattern"></div>
    <p class="back-name">Birchline<br>Septic Solutions</p>
  </section>

  <section class="card card--front" aria-label="Card front">
    <p class="brand-name">Birchline<br>Septic Solutions</p>
    <div class="divider"></div>
    <div class="contact">
      <p class="contact__name"><span class="contact__first">Colin</span> Vandro</p>
      <p class="contact__city">Cedarvale, OH</p>
      <p class="contact__phone">
        <svg viewBox="0 0 24 24" aria-hidden="true"><path fill="#27bfb8" d="M6.6 10.8a15.1 15.1 0 0 0 6.6 6.6l2.2-2.2c.3-.3.7-.4 1-.2 1.1.4 2.3.6 3.6.6.6 0 1 .4 1 1V20c0 .6-.4 1-1 1A17 17 0 0 1 3 4c0-.6.4-1 1-1h3.5c.6 0 1 .4 1 1 0 1.3.2 2.5.6 3.6.1.3 0 .7-.2 1z"/></svg>
        555-241-0387
      </p>
    </div>
    <div class="services-band">
      <span class="dot"></span>Pumping
      <span class="dot"></span>Inspections
      <span class="dot"></span>Installs
      <span class="dot"></span>And Repairs
    </div>
    <div class="services-badge">SERVICES</div>
  </section>
</main>
</body>
</html>
```